Business card por a urban DJ, up scale audience target

Need a sober design, modern, conservative colors but i can consider some options, y play rnb, hip hop, EDM and top40.

Business card for contact and personal info, double sided, use logo attrached please; im 42 so i need a card acording to my age an target audience.

Target Market(s)

Adult people, up scale audience

Industry/Entity Type

Music Download

Contact Information for Business Card

Cel (318) 4207265518 www.lumadrift.com

Requirements
Must have
• open mind
Nice to have
• open mind
Should not have
• DJ

```html
<!DOCTYPE html>
<html lang="en">
<head>
<meta charset="UTF-8">
<title>LUMA – Business Card</title>
<link href="https://fonts.googleapis.com/css2?family=Exo+2:wght@400;800&display=swap" rel="stylesheet">
<style>
  :root {
    --backdrop: #a3a3a3;
    --card-dark: #2f2f2f;
    --ink-dark: #222222;
    --ink-light: #e4e4e4;
    --photo-light: #e9e9e9;
    --photo-mid: #8a8a8a;
    --photo-deep: #1f1f1f;
  }
  * { box-sizing: border-box; margin: 0; padding: 0; }
  html, body {
    width: 1200px;
    height: 750px;
    overflow: hidden;
  }
  body {
    background: var(--backdrop);
    font-family: "Exo 2", sans-serif;
    display: flex;
    align-items: center;
    justify-content: center;
    gap: 60px;
  }
  .card {
    position: relative;
    width: 440px;
    height: 250px;
    border-radius: 22px;
    overflow: hidden;
    box-shadow: 0 10px 24px rgba(0, 0, 0, 0.28);
  }
  /* Front side */
  .card-front .crowd-photo {
    position: absolute;
    inset: 0;
    background:
      radial-gradient(ellipse at 45% 15%, var(--photo-light) 0%, rgba(233,233,233,0) 55%),
      linear-gradient(180deg, #c9c9c9 0%, var(--photo-mid) 45%, var(--photo-deep) 100%);
  }
  .front-content {
    position: relative;
    height: 100%;
    display: flex;
    flex-direction: column;
    align-items: center;
    padding-top: 34px;
  }
  .brand-name {
    font-weight: 800;
    font-size: 56px;
    letter-spacing: 4px;
    line-height: 1;
    color: var(--ink-dark);
  }
  .genres {
    margin-top: 8px;
    padding-top: 6px;
    border-top: 1.5px solid var(--ink-dark);
    font-weight: 400;
    font-size: 12px;
    letter-spacing: 4px;
    color: var(--ink-dark);
  }
  .contact-list {
    list-style: none;
    margin-top: 26px;
    display: flex;
    flex-direction: column;
    gap: 9px;
  }
  .contact-item {
    display: flex;
    align-items: center;
    gap: 10px;
    font-weight: 400;
    font-size: 17px;
    letter-spacing: 1.5px;
    color: var(--ink-light);
  }
  .contact-icon { width: 14px; height: 14px; flex: none; }
  /* Back side */
  .card-back {
    background: var(--card-dark);
    display: flex;
    align-items: center;
    justify-content: center;
  }
  .card-back .brand-name {
    font-size: 84px;
    letter-spacing: 6px;
    color: var(--ink-light);
  }
</style>
</head>
<body>
  <section class="card card-front">
    <div class="crowd-photo" role="img" aria-label="Black and white photo of a concert crowd with raised hands under stage lights"></div>
    <div class="front-content">
      <h1 class="brand-name">LUMA</h1>
      <p class="genres">RNB HIPHOP EDM</p>
      <ul class="contact-list">
        <li class="contact-item">
          <svg class="contact-icon" viewBox="0 0 14 14" aria-hidden="true">
            <rect x="3.5" y="0.8" width="7" height="12.4" rx="1.4" fill="none" stroke="currentColor" stroke-width="1.3"/>
            <circle cx="7" cy="11" r="0.8" fill="currentColor"/>
          </svg>
          (318) 4207265518
        </li>
        <li class="contact-item">
          <svg class="contact-icon" viewBox="0 0 14 14" aria-hidden="true">
            <circle cx="7" cy="7" r="6" fill="none" stroke="currentColor" stroke-width="1.2"/>
            <ellipse cx="7" cy="7" rx="2.6" ry="6" fill="none" stroke="currentColor" stroke-width="1"/>
            <line x1="1" y1="7" x2="13" y2="7" stroke="currentColor" stroke-width="1"/>
          </svg>
          www.lumadrift.com
        </li>
      </ul>
    </div>
  </section>

  <section class="card card-back">
    <p class="brand-name">LUMA</p>
  </section>
</body>
</html>
```